Ward Compass Business Card Design*

We need a business card design for our company Ward Compass. Our company is specialized in providing online consulting services regarding medical institutions, hospitals and doctors. We work with patients worldwide looking to choose between healthcare providers. We have a website you may use as a reference, where we list doctors and clinics worldwide. So we target Medical providers as well as patients worldwide.
Target Market(s)
Medical Providers and patients around the world
Industry/Entity Type
Medical
Contact Information for Business Card
Salwa Kettani
CEO
+90 612 348 2175
info@wardcompass.example
www.wardcompass.example
14 Annakhil 7 H.R.B. Rabat, Morocco
Requirements
Must have
- Company logo/name on one full side, personal info and smaller logo and company name on the other side.
Nice to have
- Smart and elegant design

```html
<!DOCTYPE html>
<html lang="en">
<head>
<meta charset="utf-8">
<title>Ward Compass — Business Card</title>
<link rel="stylesheet" href="https://fonts.googleapis.com/css2?family=Montserrat:wght@300;400;500;700&display=swap">
<style>
  :root {
    --navy: #123a6b;
    --navy-deep: #0f3160;
    --navy-light: #1a4880;
    --white: #ffffff;
    --ink: #3a3a3a;
    --grey: #8a8a8a;
    --rule: #d4d4d4;
    --stage: #2b2b2b;
  }
  * { box-sizing: border-box; margin: 0; padding: 0; }
  html, body {
    width: 1200px; height: 900px; overflow: hidden;
    background: var(--stage);
    font-family: "Montserrat", sans-serif;
  }
  .canvas {
    width: 1200px; height: 900px;
    display: flex; align-items: center; justify-content: center; gap: 80px;
  }
  .card {
    width: 360px; height: 600px;
    border-radius: 26px;
    position: relative; overflow: hidden;
    box-shadow: 0 20px 40px rgba(0,0,0,.45);
  }
  /* Front side */
  .card-front {
    background: var(--navy);
    color: var(--white);
  }
  .front-texture {
    position: absolute; inset: 0;
    background: linear-gradient(160deg, var(--navy-deep) 0%, var(--navy-light) 55%, var(--navy-deep) 100%);
  }
  .front-brand {
    position: absolute; left: 0; right: 0; top: 200px;
    display: flex; flex-direction: column; align-items: center; gap: 34px;
  }
  .brand-dot {
    width: 120px; height: 120px; border-radius: 50%;
    background: var(--white);
  }
  .front-name {
    font-weight: 500; font-size: 30px; letter-spacing: 2px;
    text-transform: uppercase;
  }
  /* Back side */
  .card-back {
    background: var(--white);
    color: var(--ink);
    display: flex; flex-direction: column; align-items: center;
    padding-top: 90px; text-align: center;
  }
  .back-brand {
    display: flex; flex-direction: column; align-items: center; gap: 14px;
  }
  .back-brand .brand-dot {
    width: 84px; height: 84px; background: var(--navy);
  }
  .back-brand-name {
    font-weight: 500; font-size: 15px; letter-spacing: 1.5px;
    color: var(--navy); text-transform: uppercase;
  }
  .person-name {
    margin-top: 56px;
    font-weight: 500; font-size: 30px; color: var(--navy);
  }
  .person-role {
    margin-top: 8px; font-weight: 300; font-size: 15px; letter-spacing: 1px;
  }
  .person-company {
    margin-top: 4px; font-weight: 300; font-size: 15px; letter-spacing: 1px;
  }
  .rule {
    width: 230px; height: 1px; background: var(--rule); margin: 18px 0;
  }
  .contact-icons { display: flex; gap: 8px; }
  .contact-icon {
    width: 28px; height: 28px; border-radius: 50%;
    background: var(--navy);
    display: flex; align-items: center; justify-content: center;
  }
  .contact-list {
    list-style: none; margin-top: 16px;
    font-weight: 400; font-size: 13.5px; letter-spacing: .8px;
    line-height: 1.7; text-transform: uppercase;
  }
</style>
</head>
<body>
<main class="canvas">
  <section class="card card-front" aria-label="Card front">
    <div class="front-texture" role="img" aria-label="Faint repeating brand-mark texture across the navy background"></div>
    <div class="front-brand">
      <span class="brand-dot"></span>
      <span class="front-name">Ward Compass</span>
    </div>
  </section>

  <section class="card card-back" aria-label="Card back">
    <div class="back-brand">
      <span class="brand-dot"></span>
      <span class="back-brand-name">Ward Compass</span>
    </div>
    <h1 class="person-name">Salwa Kettani</h1>
    <p class="person-role">CEO</p>
    <p class="person-company">WARDCOMPASS</p>
    <div class="rule"></div>
    <div class="contact-icons">
      <span class="contact-icon">
        <svg width="14" height="14" viewBox="0 0 24 24" fill="#fff"><path d="M6.6 10.8a15.1 15.1 0 0 0 6.6 6.6l2.2-2.2a1 1 0 0 1 1-.25 11.4 11.4 0 0 0 3.6.57 1 1 0 0 1 1 1V20a1 1 0 0 1-1 1A17 17 0 0 1 3 4a1 1 0 0 1 1-1h3.5a1 1 0 0 1 1 1c0 1.25.2 2.45.57 3.57a1 1 0 0 1-.25 1z"/></svg>
      </span>
      <span class="contact-icon">
        <svg width="14" height="14" viewBox="0 0 24 24" fill="#fff"><path d="M3 5h18v14H3z M3 5l9 7 9-7" stroke="#123a6b" stroke-width="1.5"/></svg>
      </span>
      <span class="contact-icon">
        <svg width="16" height="16" viewBox="0 0 24 24" fill="none" stroke="#fff" stroke-width="1.6"><circle cx="12" cy="12" r="9"/><ellipse cx="12" cy="12" rx="4" ry="9"/><path d="M3 12h18M5 7h14M5 17h14"/></svg>
      </span>
    </div>
    <ul class="contact-list">
      <li>+90 612 348 2175</li>
      <li>info@wardcompass.example</li>
      <li>www.wardcompass.example</li>
    </ul>
    <div class="rule"></div>
  </section>
</main>
</body>
</html>
```